Mindfulness School for Children -- Business Cards

We're looking for business cards for our school directors and owners. We're a mindfulness school for children called little lanterns. Attached are our logos/icons.

```html
<!DOCTYPE html>
<html lang="en">
<head>
<meta charset="utf-8">
<title>Little Lanterns — Business Cards</title>
<link href="https://fonts.googleapis.com/css2?family=Arimo:wght@400;700&display=swap" rel="stylesheet">
<style>
  :root {
    --backdrop: #c9c9c9;
    --card: #262626;
    --card-deep: #0f0f10;
    --pattern-light: #5c5c5c;
    --teal: #4aa9c0;
    --mint: #7fcfb2;
    --text: #f2f2f2;
    --white: #ffffff;
  }
  * { box-sizing: border-box; margin: 0; padding: 0; }
  html, body { width: 1200px; height: 788px; overflow: hidden; }
  body {
    background: var(--backdrop);
    font-family: "Arimo", Arial, sans-serif;
    display: flex;
    align-items: center;
    justify-content: center;
    gap: 40px;
  }
  .card {
    position: relative;
    width: 540px;
    height: 309px;
    overflow: hidden;
    box-shadow: 0 10px 24px rgba(0,0,0,.25);
  }
  .card-front { background: var(--card); color: var(--text); }
  .brand {
    position: absolute;
    display: flex;
    align-items: center;
    gap: 8px;
    color: var(--teal);
    font-weight: 400;
    letter-spacing: .5px;
  }
  .brand-dot {
    border-radius: 50%;
    background: var(--teal);
  }
  .card-front .brand { left: 250px; top: 72px; font-size: 28px; }
  .card-front .brand-dot { width: 14px; height: 14px; }
  .contact { position: absolute; left: 40px; top: 150px; }
  .contact-name {
    font-size: 21px;
    font-weight: 700;
    color: var(--teal);
    letter-spacing: .5px;
    text-transform: uppercase;
  }
  .contact-role { font-size: 12px; margin: 3px 0 8px; }
  .contact-list { list-style: none; font-size: 11.5px; line-height: 17px; }
  .contact-list li { display: flex; align-items: center; gap: 7px; }
  .contact-list svg { width: 10px; height: 10px; flex: none; }
  .divider {
    position: absolute;
    left: 40px; right: 30px; top: 250px;
    height: 1px;
    background: var(--teal);
  }
  .address { position: absolute; left: 40px; top: 266px; font-size: 12px; }
  .edge-accent {
    position: absolute; left: 0; bottom: 0;
    width: 28px; height: 8px;
    background: var(--teal);
  }
  .edge-band {
    position: absolute; left: 34px; right: 0; bottom: 0;
    height: 8px;
    background: var(--white);
  }
  .card-back .pattern {
    position: absolute; inset: 0;
    background: linear-gradient(30deg, var(--card-deep) 0%, #1b1b1c 45%, var(--pattern-light) 100%);
  }
  .card-back .brand { right: 28px; bottom: 52px; font-size: 34px; }
  .card-back .brand-dot { width: 16px; height: 16px; }
</style>
</head>
<body>
  <section class="card card-front" aria-label="Business card front">
    <div class="brand"><span class="brand-dot"></span>littlelanterns</div>

    <div class="contact">
      <h1 class="contact-name">Nora Whitfield</h1>
      <p class="contact-role">CEO/Founder</p>
      <ul class="contact-list">
        <li>
          <svg viewBox="0 0 10 10" aria-hidden="true"><path d="M2 1 L4 1 L4.6 3 L3.4 3.8 Q4.4 5.8 6.2 6.6 L7 5.4 L9 6 L9 8 Q5 9 2 6 Q0.8 4 2 1Z" fill="var(--teal)"/></svg>
          (00) 5296 3187
        </li>
        <li>
          <svg viewBox="0 0 10 10" aria-hidden="true"><rect x="0.5" y="2" width="9" height="6" fill="none" stroke="var(--teal)" stroke-width="1"/><path d="M0.5 2 L5 5.5 L9.5 2" fill="none" stroke="var(--teal)" stroke-width="1"/></svg>
          info@littlelanterns.com
        </li>
        <li>
          <svg viewBox="0 0 10 10" aria-hidden="true"><circle cx="5" cy="5" r="4.3" fill="var(--teal)"/></svg>
          www.littlelanterns.com
        </li>
      </ul>
    </div>

    <div class="divider"></div>
    <p class="address">Po Box 4120 Elm Street Country Name, AB 36912</p>
    <div class="edge-accent"></div>
    <div class="edge-band"></div>
  </section>

  <section class="card card-back" aria-label="Business card back">
    <div class="pattern" role="img" aria-label="Repeating embossed flower pattern in glossy black and grey"></div>
    <div class="brand"><span class="brand-dot"></span>littlelanterns</div>
  </section>
</body>
</html>
```